Business Card Design

My business is writing crime novels to entertain readers. I write legal thrillers and mysteries. I need a card for publishers, agents, other authors, and media.

Industry/Entity Type

Legal

Contact Information for Business Card

Paul Derrow
www.derrowfiction.example
pauljderrow@inkpost.example
0064 27 5190472

```html
<!DOCTYPE html>
<html lang="en">
<head>
<meta charset="utf-8">
<title>Paul Derrow – Business Card</title>
<link rel="stylesheet" href="https://fonts.googleapis.com/css2?family=Tinos&display=swap">
<style>
  :root {
    --page-bg: #ececec;
    --card-paper: #dddddb;
    --card-paper-light: #e6e6e4;
    --linen-thread-dark: rgba(0, 0, 0, 0.045);
    --linen-thread-light: rgba(255, 255, 255, 0.35);
    --ink: #141414;
    --arc-black: #050505;
    --arc-dark: #1c1c1c;
    --arc-mid: #333333;
    --portrait-shadow: #121212;
    --portrait-mid: #3c3c3c;
    --portrait-light: #9a9a9a;
    --portrait-rim: rgba(255, 255, 255, 0.12);
  }
  * { margin: 0; padding: 0; box-sizing: border-box; }
  html, body {
    width: 1200px;
    height: 800px;
    overflow: hidden;
    background: var(--page-bg);
  }
  .canvas {
    width: 1200px;
    height: 800px;
    display: flex;
    align-items: center;
    justify-content: center;
  }
  .business-card {
    position: relative;
    width: 1000px;
    height: 500px;
    background-color: var(--card-paper);
    background-image:
      repeating-linear-gradient(0deg, var(--linen-thread-dark) 0 1px, transparent 1px 3px),
      repeating-linear-gradient(90deg, var(--linen-thread-dark) 0 1px, transparent 1px 3px),
      repeating-linear-gradient(90deg, var(--linen-thread-light) 0 1px, transparent 1px 5px),
      linear-gradient(135deg, var(--card-paper-light), var(--card-paper));
    overflow: hidden;
    box-shadow: 0 6px 18px rgba(0, 0, 0, 0.12);
  }
  .card-contact {
    position: absolute;
    left: 300px;
    top: 180px;
    transform: translateX(-50%);
    text-align: center;
    font-family: "Tinos", "Times New Roman", serif;
    color: var(--ink);
    white-space: nowrap;
  }
  .author-name {
    font-size: 46px;
    font-weight: 400;
    font-variant: small-caps;
    letter-spacing: 4px;
    margin-bottom: 8px;
  }
  .contact-line {
    font-size: 23px;
    line-height: 30px;
  }
  .card-arcs {
    position: absolute;
    inset: 0;
    width: 1000px;
    height: 500px;
  }
</style>
</head>
<body>
<main class="canvas">
  <section class="business-card">
    <div class="card-contact">
      <h1 class="author-name">Paul Derrow</h1>
      <p class="contact-line">www.derrowfiction.example</p>
      <p class="contact-line">pauljderrow@inkpost.example</p>
      <p class="contact-line">0064 27 5190472</p>
    </div>

    <svg class="card-arcs" viewBox="0 0 1000 500" xmlns="http://www.w3.org/2000/svg">
      <defs>
        <linearGradient id="arc-layer-shade" x1="0" y1="0" x2="1" y2="0">
          <stop offset="0" stop-color="var(--arc-dark)"/>
          <stop offset="1" stop-color="var(--arc-mid)"/>
        </linearGradient>
        <radialGradient id="portrait-backdrop" cx="0.62" cy="0.3" r="0.8">
          <stop offset="0" stop-color="var(--portrait-light)"/>
          <stop offset="0.55" stop-color="var(--portrait-mid)"/>
          <stop offset="1" stop-color="var(--portrait-shadow)"/>
        </radialGradient>
      </defs>
      <path class="arc-outer" d="M672,0 Q470,200 478,500 L1000,500 L1000,0 Z" fill="var(--arc-black)"/>
      <path class="arc-middle" d="M702,0 Q520,210 532,500 L1000,500 L1000,0 Z" fill="url(#arc-layer-shade)"/>
      <path class="arc-inner" d="M730,0 Q565,220 578,500 L1000,500 L1000,0 Z" fill="var(--arc-black)"/>
      <g role="img" aria-label="Portrait photograph of the author in a black leather jacket and white shirt, against a dark grey studio backdrop">
        <path class="portrait-area" d="M745,0 Q590,225 602,500 L1000,500 L1000,0 Z" fill="url(#portrait-backdrop)"/>
        <path class="portrait-rim" d="M745,0 Q590,225 602,500" fill="none" stroke="var(--portrait-rim)" stroke-width="2"/>
      </g>
    </svg>
  </section>
</main>
</body>
</html>
```